BRTL web site redesign

Coastal Linkage Engineering service (BRTL) is a diverse technology company specialising in design and installation of fibre optics, network convergence and building services, for commercial clients in Australia, we required a new design of our website to attract new clients, generate sales leads, and provide information about our services to the market. The site and should have a new technology look and feel and be designed in word press. our branding colour is blue.

Target Market(s)

New developments, Construction organisations, Commercial end users, IT managers, Consultants.

Industry/Entity Type

It Company

Number of Pages Required

5+ page

Font styles to use
Sans Serif

Colors
0292cd
3176b5

Requirements
Must have
• key pages.
• Home page with some sizzle, automated pictures running through, I like the look of this competitor website http://www.gleamwirex.com.au/ good clean menus and easy to navigate.
• Services page our key services are Fibre optics, Security, Building services,Electrical. I would like the same page layout (Design) for all our services, with a find out more link on each page, manly picture driven with text around our key messaging.
• About us page with space for company profile and directors pictures, bio and contact information.
• Certifications / Accreditations page with have over 20 certifications on different products from suppliers, and a number of licences from governing bodies.
• Current and past projects page with case studies and customer outcomes
• Contact us page with options around what services they require more information on, please keep in mind the site is around generating sales Leeds and being seen as an industry expert.
Nice to have
• RSS feeds, Linked in link, to be placed within the design, Consistent BRTL branding,Same colour blue as our logo Document library for education information, white papers, presentations etc,
• a new technology look and feel, mobile friendly.
Should not have
• boring layout, move away from our cuurent website http://www.brtlgroup.com.au/
• no e eCommerce store required.

```html
<!DOCTYPE html>
<html lang="en">
<head>
<meta charset="utf-8">
<title>BRTL – Coastal Linkage Engineering Service</title>
<link rel="stylesheet" href="https://fonts.googleapis.com/css2?family=Open+Sans:wght@400;600;700&display=swap">
<style>
  :root{
    --brand:#0894cb;
    --brand-deep:#3176b5;
    --link:#1a9ad6;
    --ink:#2b2b2b;
    --muted:#444;
    --white:#fff;
    --night:#050708;
    --footer:#0b0b0b;
  }
  *{margin:0;padding:0;box-sizing:border-box;}
  html,body{width:710px;height:1200px;overflow:hidden;background:var(--white);}
  body{font-family:"Open Sans",Arial,sans-serif;color:var(--ink);position:relative;}
  .abs{position:absolute;}

  /* header */
  .site-header{left:0;top:0;width:710px;height:78px;background:var(--brand);box-shadow:0 2px 3px rgba(0,0,0,.35);z-index:2;}
  .brand-box{left:31px;top:6px;width:130px;height:66px;background:var(--white);border:3px solid var(--white);outline:1px solid #0a6fa0;display:flex;flex-direction:column;align-items:center;justify-content:center;}
  .brand-name{font-size:30px;font-weight:700;color:var(--brand-deep);line-height:1;letter-spacing:1px;display:flex;align-items:center;gap:6px;}
  .brand-mark{width:10px;height:10px;background:var(--brand);}
  .brand-sub{font-size:5px;font-weight:700;color:var(--brand-deep);margin-top:5px;text-transform:uppercase;white-space:nowrap;}
  .main-nav a{position:absolute;top:31px;font-size:7.6px;font-weight:600;color:var(--white);text-decoration:none;white-space:nowrap;}

  /* hero */
  .hero{left:0;top:78px;width:710px;height:272px;
    background:
      radial-gradient(ellipse 70px 120px at 4% 30%,rgba(214,196,96,.75),rgba(214,196,96,0) 100%),
      radial-gradient(ellipse 150px 200px at 86% 70%,rgba(28,30,36,.95),rgba(28,30,36,0) 100%),
      radial-gradient(ellipse 60px 50px at 82% 22%,rgba(200,160,130,.55),rgba(200,160,130,0) 100%),
      linear-gradient(90deg,#7d858c 0%,#a8afb5 12%,#6f767d 22%,#b9bec3 34%,#8c9399 46%,#5c6369 57%,#d8dbde 62%,#e4e6e8 74%,#d6d8db 100%);}
  .hero-caption{left:0;top:302px;width:710px;height:48px;background:rgba(40,40,40,.82);}
  .hero-caption p{position:absolute;left:31px;top:17px;font-size:10.4px;font-weight:600;color:var(--white);text-transform:uppercase;}
  .slider-dots{left:638px;top:325px;display:flex;gap:2.5px;}
  .slider-dots span{width:4.5px;height:4.5px;border:1px solid var(--white);}
  .slider-dots span:first-child{background:var(--white);}

  /* about */
  .section-title{font-size:14px;font-weight:400;color:#222;text-shadow:0 1px 1px rgba(0,0,0,.15);}
  .about-text{left:31px;top:410px;width:634px;font-size:7.1px;line-height:13px;color:var(--muted);}

  .service{width:150px;}
  .service-photo{width:144px;height:92px;border:1px solid #222;box-shadow:1px 1px 3px rgba(0,0,0,.4);}
  .service h3{margin-top:9px;font-size:11px;font-weight:400;color:var(--link);}
  .service p{margin-top:3px;width:128px;font-size:6.9px;line-height:13px;color:var(--muted);}
  .btn-small{display:inline-block;margin-top:5px;padding:0 6px;height:21px;line-height:21px;font-size:6.4px;font-weight:600;color:var(--white);background:var(--brand);box-shadow:0 2px 2px rgba(0,0,0,.4);text-decoration:none;}

  .photo-fibre{background:
      radial-gradient(ellipse 40px 20px at 30% 25%,rgba(230,130,60,.85),rgba(230,130,60,0)),
      radial-gradient(ellipse 35px 30px at 78% 45%,rgba(40,140,210,.85),rgba(40,140,210,0)),
      radial-gradient(ellipse 30px 25px at 15% 70%,rgba(80,170,80,.7),rgba(80,170,80,0)),
      linear-gradient(135deg,#3a3836,#2a2c30 50%,#5b4a3c);}
  .photo-security{background:
      radial-gradient(ellipse 30px 40px at 30% 35%,rgba(235,235,240,.9),rgba(235,235,240,0)),
      radial-gradient(ellipse 35px 25px at 80% 30%,rgba(245,245,248,.9),rgba(245,245,248,0)),
      radial-gradient(ellipse 25px 40px at 55% 60%,rgba(200,200,205,.8),rgba(200,200,205,0)),
      linear-gradient(160deg,#1c1b22,#4a4856 55%,#15141a);}
  .photo-building{background:
      radial-gradient(ellipse 45px 35px at 70% 35%,rgba(140,220,255,.85),rgba(140,220,255,0)),
      radial-gradient(ellipse 35px 45px at 25% 70%,rgba(20,40,70,.85),rgba(20,40,70,0)),
      linear-gradient(135deg,#0a5a9a,#2b9ad8 55%,#0d3f78);}
  .photo-electrical{background:
      radial-gradient(ellipse 50px 20px at 50% 12%,rgba(120,115,108,.8),rgba(120,115,108,0)),
      radial-gradient(ellipse 30px 30px at 45% 55%,rgba(196,160,110,.7),rgba(196,160,110,0)),
      radial-gradient(ellipse 25px 40px at 85% 60%,rgba(236,236,232,.9),rgba(236,236,232,0)),
      linear-gradient(90deg,#6c6a66,#bdb8ae 25%,#8d877e 50%,#d4d0c8 75%,#a29c92);}

  /* feature band */
  .feature{left:0;top:697px;width:710px;height:190px;
    background:
      radial-gradient(ellipse 140px 190px at 14% 60%,rgba(60,140,170,.75),rgba(60,140,170,0)),
      radial-gradient(ellipse 260px 170px at 25% 30%,#184a62 0%,#0b2230 45%,rgba(5,7,8,0) 100%),
      var(--night);}
  .feature h2{position:absolute;left:0;width:710px;top:44px;text-align:center;font-size:18px;font-weight:400;color:var(--white);}
  .feature hr{position:absolute;left:141px;top:75px;width:429px;border:0;border-top:1px solid #555;}
  .feature p{position:absolute;left:180px;width:350px;top:85px;text-align:center;font-size:7.2px;line-height:13.5px;color:var(--white);}
  .btn-outline{position:absolute;left:314px;top:123px;width:82px;height:22px;border:1px solid var(--white);color:var(--white);font-size:10px;line-height:20px;text-align:center;text-decoration:none;}

  /* projects */
  .project{width:170px;}
  .project h4{font-size:8px;font-weight:400;color:var(--link);white-space:nowrap;}
  .project time{display:block;margin-top:4px;font-size:6.8px;color:#222;}
  .project p{margin-top:4px;width:160px;font-size:7px;line-height:13.2px;color:var(--muted);}

  .site-footer{left:0;top:1162px;width:710px;height:38px;background:var(--footer);color:var(--white);font-size:6.8px;text-align:center;line-height:38px;}
</style>
</head>
<body>

<header class="site-header abs">
  <div class="brand-box abs">
    <div class="brand-name"><span class="brand-mark"></span>BRTL</div>
    <div class="brand-sub">Coastal Linkage Engineering Service</div>
  </div>
  <nav class="main-nav">
    <a style="left:274px">HOME</a>
    <a style="left:318px">SERVICES</a>
    <a style="left:375px">ABOUT US</a>
    <a style="left:434px">CERTIFICATIONS</a>
    <a style="left:514px">CURRENT / PAST PROJECTS</a>
    <a style="left:634px">CONTACT US</a>
  </nav>
</header>

<section class="hero abs" role="img" aria-label="Engineer with a laptop beside a server rack in a data centre"></section>
<div class="hero-caption abs"><p>BRTL is diversified technology company 100% Australian owned and operated</p></div>
<div class="slider-dots abs"><span></span><span></span><span></span><span></span><span></span></div>

<h2 class="section-title abs" style="left:32px;top:373px">About BRTL Group</h2>
<p class="about-text abs">BRTL is diversified technology company 100% Australian owned and operated, we provide Communication, Electrical, Security &amp; ICT services for residential and commercial customers. With over 100 years of combined industry knowledge we pride ourselves on innovated solutions that utilises technology advancements which delivers on our customer's expectations.</p>

<article class="service abs" style="left:31px;top:468px">
  <div class="service-photo photo-fibre" role="img" aria-label="Fibre splicing equipment and cables"></div>
  <h3>Fibre Optics</h3>
  <p>Proin gravida nibh vel velit auctored aliquetenean sollicitudin lorem quis bibendum auctornisi elit.</p>
  <a class="btn-small">READ MORE</a>
</article>
<article class="service abs" style="left:200px;top:468px">
  <div class="service-photo photo-security" role="img" aria-label="Security cameras on a pole"></div>
  <h3>Security</h3>
  <p>Proin gravida nibh vel velit auctored aliquetenean sollicitudin lorem quis bibendum auctornisi elit.</p>
  <a class="btn-small">READ MORE</a>
</article>
<article class="service abs" style="left:369px;top:468px">
  <div class="service-photo photo-building" role="img" aria-label="Person using a building control touch screen"></div>
  <h3>Building Services</h3>
  <p>Proin gravida nibh vel velit auctored aliquetenean sollicitudin lorem quis bibendum auctornisi elit.</p>
  <a class="btn-small">READ MORE</a>
</article>
<article class="service abs" style="left:535px;top:468px">
  <div class="service-photo photo-electrical" role="img" aria-label="Electrical conduits and switchgear"></div>
  <h3>Electrical</h3>
  <p>Proin gravida nibh vel velit auctored aliquetenean sollicitudin lorem quis bibendum auctornisi elit.</p>
  <a class="btn-small">READ MORE</a>
</article>

<section class="feature abs" role="img" aria-label="Glowing fibre optic strands on a dark background">
  <h2>BRTL offers a wide range of IP commercial security solutions</h2>
  <hr>
  <p>Proin gravida nibh vel velit auctor aliquet. Aenean sollicitudin, lorem quis bibendum auctor, nisi elit consequat ipsum, nec sagittis sem nibh id elit.</p>
  <a class="btn-outline">READ MORE</a>
</section>

<h2 class="section-title abs" style="left:31px;top:910px">Current / Past Projects</h2>

<article class="project abs" style="left:52px;top:953px"><h4>Proin gravida nibh vel velit auctor aliquet</h4><time>12 Jan 2015</time><p>Lorem Ipsum. Proin gravida nibh vel velit ws uctor aliquet lorem quis bibendum auctor nisi elit consequat ipsum nec sagitti,</p></article>
<article class="project abs" style="left:269px;top:953px"><h4>Gravida nibh vel velit auctor aliquet vild</h4><time>12 Jan 2015</time><p>Lorem Ipsum. Proin gravida nibh vel velit ws uctor aliquet lorem quis bibendum auctor nisi elit consequat ipsum nec sagitti,</p></article>
<article class="project abs" style="left:494px;top:953px"><h4>Hroin gravida nibh vel velit auctor aliquet</h4><time>12 Jan 2015</time><p>Lorem Ipsum. Proin gravida nibh vel velit ws uctor aliquet lorem quis bibendum auctor nisi elit consequat ipsum nec sagitti,</p></article>
<article class="project abs" style="left:52px;top:1052px"><h4>Aroin gravida nibh vel velit auctor aliquet</h4><time>10 Jan 2015</time><p>Lorem Ipsum. Proin gravida nibh vel velit ws uctor aliquet lorem quis bibendum auctor nisi elit consequat ipsum nec sagitti,</p></article>
<article class="project abs" style="left:269px;top:1052px"><h4>Proin gravida nibh vel velit auctor aliquet</h4><time>10 Jan 2015</time><p>Lorem Ipsum. Proin gravida nibh vel velit ws uctor aliquet lorem quis bibendum auctor nisi elit consequat ipsum nec sagitti,</p></article>
<article class="project abs" style="left:494px;top:1052px"><h4>Aravida nibh vel velit auctor aliquet seed</h4><time>10 Jan 2015</time><p>Lorem Ipsum. Proin gravida nibh vel velit ws uctor aliquet lorem quis bibendum auctor nisi elit consequat ipsum nec sagitti,</p></article>

<footer class="site-footer abs">©Copyright 2014 &nbsp;brtlgroup &nbsp; | &nbsp; All rights reserved &nbsp; | &nbsp; Privacy policy &nbsp; | &nbsp; Terms &amp; Conditions</footer>

</body>
</html>
```